Brand new redesign of Brightpath finance website

I need a new website design that i can advertise a great low interest rate on the front page and capture input application details that will send through to my email address.

some car finance companies will be similar to this would be listed below

tallowcredit.example.com.au
mirabelfinance.example.com.au
finance725.example.com.au
quenbyfinance.example.com.au
finance91.example.com.au

Reason: I have changed the project to a committed project. all the webpages should have the same format just different content and i want to be able to edit the front page easily to update my interest rates.

Target Market(s)

Australian Finance market targeting a younger demographic

Industry/Entity Type

Finance

Coding

Coded - Design and coding required

Number of Pages Required

5+ page

Font styles to use
Serif
Sans Serif

Colors
0255a3
ffffff
cedeed

Requirements
Must have
• application capture form
• apply now buttons
• Headline rate front page

```html
<!DOCTYPE html>
<html lang="en">
<head>
<meta charset="utf-8">
<title>Brightpath Finance</title>
<link href="https://fonts.googleapis.com/css2?family=Lato:wght@400;700&family=Roboto+Condensed:wght@400;700&display=swap" rel="stylesheet">
<style>
:root{
  --blue:#1e56a6;
  --blue-deep:#0255a3;
  --blue-band:#2260b0;
  --ink:#231f20;
  --pale:#cedeed;
  --white:#ffffff;
  --grey-text:#5a5a5a;
  --dark:#2a2a2a;
}
*{margin:0;padding:0;box-sizing:border-box}
html,body{width:815px;height:1200px;overflow:hidden;background:var(--white)}
body{position:relative;font-family:'Lato',sans-serif;color:var(--ink)}
.abs{position:absolute}
.cond{font-family:'Roboto Condensed',sans-serif}

.topbar{left:0;top:0;width:815px;height:29px;background:var(--ink)}
.topbar .call{left:474px;top:8px;font-size:10px;color:var(--white)}
.topbar .call b{font-weight:400;font-size:11px}
.social-dot{width:20px;height:20px;border-radius:50%;background:#000;border:1px solid #444}

.header{left:0;top:29px;width:815px;height:70px;background:var(--white)}
.brand{left:88px;top:38px;display:flex;align-items:center;gap:7px}
.brand .mark{width:22px;height:22px;border-radius:50%;background:#7a7a7a}
.brand .name{font-family:'Roboto Condensed',sans-serif;font-weight:700;font-size:15px;color:#6d6d6d;line-height:1.05}
.nav{top:52px;font-family:'Roboto Condensed',sans-serif;font-size:11px;color:var(--ink);line-height:24px}
.nav.home{left:212px;width:47px;height:24px;background:var(--blue);color:var(--white);border-radius:12px;text-align:center}
.nav.apply{left:662px;width:59px;height:23px;background:var(--ink);color:var(--white);text-align:center;font-weight:700}

.hero{left:0;top:99px;width:815px;height:291px;background:linear-gradient(100deg,#3c6bb0 0%,#5a86c4 35%,#3e6fb6 60%,#2a5aa3 100%)}
.hero-title{left:109px;top:166px;font-size:24px;font-weight:700;color:var(--white);line-height:28px}
.rate-label{left:115px;top:236px;font-size:19px;font-weight:700;color:var(--white)}
.rate{left:115px;width:162px;font-size:12px;color:var(--white);border-bottom:1px solid rgba(255,255,255,.5);padding-bottom:6px}
.btn-dark{left:113px;top:325px;width:62px;height:21px;background:var(--ink);color:var(--white);font-size:10px;text-align:center;line-height:21px;border-radius:2px}

.quote{left:523px;top:134px;width:205px;height:230px;background:#18325e}
.quote svg{position:absolute;left:0;top:0}
.quote h2{position:absolute;left:0;top:10px;width:205px;text-align:center;font-family:'Roboto Condensed',sans-serif;font-size:18px;font-weight:700;color:var(--blue-deep)}
.field{left:12px;width:181px;height:22px;background:var(--white);border-radius:2px;font-size:8px;color:#777;padding-left:8px;line-height:22px}
.quote .submit{left:12px;top:192px;width:181px;height:25px;background:var(--blue);color:var(--white);text-align:center;line-height:25px;font-size:11px;font-weight:700;border-radius:2px}

.about{left:0;top:390px;width:815px;height:211px;background:linear-gradient(#f3f3f3,#fff)}
.section-title{left:0;width:815px;text-align:center;font-size:22px;font-weight:700}
.dot-icon{width:16px;height:16px;border-radius:50%}
.about p{left:92px;top:480px;width:631px;font-size:9px;line-height:15px;color:var(--grey-text);text-align:center}
.btn-blue{background:var(--blue-deep);color:var(--white);font-size:9.5px;font-weight:700;text-align:center;border-radius:2px}

.services{left:0;top:601px;width:815px;height:241px;background:var(--blue-band)}
.card{top:687px;width:149px;height:125px}
.card .photo{width:149px;height:96px}
.card .label{position:absolute;left:0;top:96px;width:149px;height:29px;background:#1c1c1c;color:var(--white);font-family:'Roboto Condensed',sans-serif;font-size:12px;line-height:29px;padding-left:55px}
.card .badge{position:absolute;left:14px;top:94px;width:34px;height:34px;border-radius:50%;background:var(--white);border:3px solid #1c1c1c;box-shadow:0 0 0 1px #fff}

.calc{left:87px;top:873px;width:641px;height:81px;background:linear-gradient(90deg,#3a3a3a,#2b3038 60%,#383c42)}
.calc h3{position:absolute;left:33px;top:19px;font-family:'Roboto Condensed',sans-serif;font-size:20px;font-weight:700;color:var(--white)}
.calc p{position:absolute;left:34px;top:50px;font-family:'Roboto Condensed',sans-serif;font-size:12px;color:var(--white)}
.calc .btn-blue{position:absolute;left:543px;top:28px;width:82px;height:22px;line-height:22px;background:#1e64c0}

.newsletter{left:0;top:984px;width:815px;height:131px;background:var(--dark)}
.news-title{left:176px;top:1016px;font-size:22px;font-weight:700;color:var(--white)}
.news-input{left:178px;top:1054px;width:239px;height:26px;background:var(--white);font-size:8px;color:#333;padding-left:8px;line-height:26px}
.news-go{left:423px;top:1054px;width:58px;height:26px;background:var(--blue);color:var(--white);font-family:'Roboto Condensed',sans-serif;font-weight:700;font-size:13px;text-align:center;line-height:26px}

.footnav{left:0;top:1115px;width:815px;height:35px;background:#000;display:flex;justify-content:center;align-items:center;gap:13px;font-family:'Roboto Condensed',sans-serif;font-size:11px;color:var(--white)}
.footnav .sep{font-size:8px;color:#aaa}

.bottombar{left:0;top:1150px;width:815px;height:50px;background:var(--blue-band)}
.copy{left:87px;top:1170px;font-size:8.5px;font-weight:700;color:var(--white)}
.follow{left:592px;top:1171px;font-size:9px;font-weight:700;color:var(--white)}
.foot-dot{width:20px;height:20px;border-radius:50%;background:var(--white);top:1165px}
</style>
</head>
<body>

<div class="abs topbar"></div>
<div class="abs topbar call" style="width:auto;height:auto;background:none;left:474px;top:8px">Worried About Finance? <b>Call 1300 555 017</b></div>
<div class="abs social-dot" style="left:636px;top:5px" aria-label="Social link"></div>
<div class="abs social-dot" style="left:659px;top:5px" aria-label="Social link"></div>
<div class="abs social-dot" style="left:682px;top:5px" aria-label="Social link"></div>
<div class="abs social-dot" style="left:706px;top:5px" aria-label="Social link"></div>

<div class="abs header"></div>
<div class="abs brand"><span class="mark"></span><span class="name">BRIGHTPATH<br>FINANCE</span></div>
<div class="abs nav home">Home</div>
<div class="abs nav" style="left:268px">About Us</div>
<div class="abs nav" style="left:324px">Services</div>
<div class="abs nav" style="left:378px">Terms Of Use</div>
<div class="abs nav" style="left:452px">Privacy Policy</div>
<div class="abs nav" style="left:527px">Loan Calculator</div>
<div class="abs nav" style="left:607px">Contact us</div>
<div class="abs nav apply">Apply Now</div>

<div class="abs hero" role="img" aria-label="Photo of a smiling mother and child in a car, tinted blue"></div>
<div class="abs hero-title">We Providing Lowest<br>Interest Rate</div>
<div class="abs rate-label">Rate :</div>
<div class="abs rate" style="top:263px">4.69%</div>
<div class="abs rate" style="top:287px">4.99%</div>
<div class="abs btn-dark">Compare</div>

<div class="abs quote">
  <svg width="205" height="45" viewBox="0 0 205 45"><path d="M0 0H205V32L102 41L0 32Z" fill="#ffffff"/></svg>
  <h2>Quick Quote</h2>
  <div class="abs field" style="top:56px">Name *</div>
  <div class="abs field" style="top:90px">Telephone *</div>
  <div class="abs field" style="top:124px">Email *</div>
  <div class="abs field" style="top:158px">Employment Status *</div>
  <div class="abs submit">APPLY NOW</div>
</div>

<div class="abs about"></div>
<div class="abs section-title" style="top:415px">About Brightpath Finance</div>
<div class="abs dot-icon" style="left:399px;top:452px;background:#8a8a8a"></div>
<p class="abs" style="left:92px;top:480px;width:631px;font-size:9px;line-height:15px;color:var(--grey-text);text-align:center">Lorem Ipsum is simply dummy text of the printing and typesetting industry. Lorem Ipsum has been the industry's standard dummy text ever since the 1500s, when an unknown printer took a galley of type and scrambled it to make a type specimen book. It has survived not only five centuries, but also the leap into electronic typesetting, remaining essentially unchanged. It was popularised in the 1960s with the release of Letraset sheets containing Lorem Ipsum passages, and more recently with desktop publishing software</p>
<div class="abs btn-blue" style="left:377px;top:551px;width:61px;height:20px;line-height:20px">Read more</div>

<div class="abs services"></div>
<div class="abs section-title" style="top:623px;color:var(--white)">Our Services</div>
<div class="abs dot-icon" style="left:399px;top:656px;background:#163f7e"></div>

<div class="abs card" style="left:87px">
  <div class="photo" role="img" aria-label="Photo of car keys being handed over" style="background:linear-gradient(135deg,#d9d2cb,#a7988c)"></div>
  <div class="label">Vehicle Loans</div><div class="badge"></div>
</div>
<div class="abs card" style="left:252px">
  <div class="photo" role="img" aria-label="Photo of a speedboat on the water" style="background:linear-gradient(#dfe8f0,#7c9ab3)"></div>
  <div class="label">Boat Loans</div><div class="badge"></div>
</div>
<div class="abs card" style="left:416px">
  <div class="photo" role="img" aria-label="Photo of a model house held in hands" style="background:linear-gradient(#4aa0e0,#d9b48c)"></div>
  <div class="label">Home Loans</div><div class="badge"></div>
</div>
<div class="abs card" style="left:580px">
  <div class="photo" role="img" aria-label="Photo of a hand stacking coins" style="background:linear-gradient(135deg,#f2f2f2,#b9b2aa)"></div>
  <div class="label">Personal Loans</div><div class="badge"></div>
</div>

<div class="abs calc" role="img" aria-label="Darkened photo background of a woman">
  <h3>What will my repayments be?</h3>
  <p>See how much you could borrow with our loan calculator.</p>
  <div class="btn-blue">Loan Calculator</div>
</div>

<div class="abs newsletter"></div>
<div class="abs" role="img" aria-label="Illustration of a waving cartoon businessman" style="left:75px;top:996px;width:70px;height:112px;background:linear-gradient(#e8e8e8,#5a4030);border-radius:30px 30px 6px 6px;opacity:.85"></div>
<div class="abs news-title">Newsletter Signup</div>
<div class="abs news-input">Enter your email</div>
<div class="abs news-go">Go</div>
<div class="abs" role="img" aria-label="Illustration of a house with blue roof and keys" style="left:550px;top:1000px;width:185px;height:105px;background:linear-gradient(135deg,#c9ccd1,#4a78c0);border-radius:8px;opacity:.85"></div>

<div class="abs footnav">
  <span>Home</span><span class="sep">::</span><span>About Us</span><span class="sep">::</span><span>Services</span><span class="sep">::</span><span>Terms Of Use</span><span class="sep">::</span><span>Privacy Policy</span><span class="sep">::</span><span>Loan Calculator</span><span class="sep">::</span><span>Contact us</span>
</div>

<div class="abs bottombar"></div>
<div class="abs copy">Copyright © 2016 Brightpathfinance &nbsp;| All rights reserved.</div>
<div class="abs follow">Follow Us</div>
<div class="abs foot-dot" style="left:638px"></div>
<div class="abs foot-dot" style="left:661px"></div>
<div class="abs foot-dot" style="left:684px"></div>
<div class="abs foot-dot" style="left:708px"></div>

</body>
</html>
```